We need a business card design for a new company located in Missouri City, TX, entitled 'BrightPath Chiropractic & Holistic Center'. Our services include restoration of health and vitality, spinal exam, health assessment, dietary & fitness programs, lymphatic & therapeutic massage, detox & remineralize body wraps, far infrared sauna therapy

Industry/Entity Type

Business

Contact Information for Business Card

BrightPath Chiropractic & Holistic Center, Marlene Okafor LMT, 4215 Elm Ridge Rd., Suite 310, Missouri City, TX 77482, 281-555-0193

```html
<!DOCTYPE html>
<html lang="en">
<head>
<meta charset="utf-8">
<title>BrightPath Chiropractic &amp; Holistic Center – Business Card</title>
<link rel="stylesheet" href="https://fonts.googleapis.com/css2?family=PT+Sans:wght@400;700&family=Gelasio:wght@500&display=swap">
<style>
  :root {
    --teal: #1b9a83;
    --navy: #1f5783;
    --ink: #1d2a2e;
    --grey: #6b6e70;
    --sky: #2b8fd3;
    --paper: #fdfdfd;
    --backdrop: #e6e8e8;
  }
  * { box-sizing: border-box; margin: 0; padding: 0; }
  html, body { width: 1200px; height: 902px; overflow: hidden; }
  body {
    background: var(--backdrop);
    font-family: "PT Sans", Arial, sans-serif;
    color: var(--ink);
    display: flex;
    flex-direction: column;
    align-items: center;
    justify-content: center;
    gap: 36px;
  }
  .card {
    width: 700px;
    height: 400px;
    background: var(--paper);
    position: relative;
    overflow: hidden;
    box-shadow: 0 4px 14px rgba(0,0,0,.12);
  }

  /* Front */
  .front__brand {
    position: absolute; left: 44px; top: 96px;
    color: var(--grey);
  }
  .brand-name {
    font-size: 44px; font-weight: 700; color: var(--grey);
    display: flex; align-items: center; gap: 12px; line-height: 1;
  }
  .brand-dot { width: 14px; height: 14px; border-radius: 50%; background: var(--teal); flex: none; }
  .brand-sub { font-size: 17px; letter-spacing: .5px; margin-top: 8px; color: var(--grey); }
  .front__person { position: absolute; right: 44px; top: 40px; text-align: right; }
  .person-name { font-family: "Gelasio", Georgia, serif; font-size: 44px; font-weight: 500; color: var(--navy); line-height: 1.1; }
  .person-role { font-size: 20px; color: var(--ink); margin-top: 2px; }
  .front__band {
    position: absolute; left: 0; right: 0; bottom: 0; height: 190px;
    background: var(--teal);
    border-top: 6px solid var(--navy);
    padding: 26px 44px;
  }
  .contact-list { list-style: none; display: flex; flex-direction: column; gap: 9px; }
  .contact-item { display: flex; align-items: center; gap: 14px; font-size: 19px; color: var(--ink); }
  .contact-icon {
    width: 20px; height: 20px; background: var(--ink); border-radius: 3px;
    display: flex; align-items: center; justify-content: center; flex: none;
  }

  /* Back */
  .back__rule {
    position: absolute; left: 150px; right: 0; top: 96px;
    height: 2px; background: var(--teal);
  }
  .back__title { position: absolute; left: 150px; top: 46px; font-size: 44px; color: var(--sky); line-height: 1; }
  .back__brand { position: absolute; left: 40px; top: 118px; }
  .back__brand .brand-name { font-size: 22px; gap: 8px; }
  .back__brand .brand-dot { width: 9px; height: 9px; }
  .service-list { position: absolute; left: 250px; top: 126px; list-style: none; display: flex; flex-direction: column; gap: 9px; }
  .service-item { display: flex; align-items: center; gap: 14px; font-size: 20px; color: var(--ink); }
  .service-bullet { width: 10px; height: 10px; border-radius: 50%; background: var(--teal); flex: none; }
</style>
</head>
<body>

  <section class="card card--back" aria-label="Business card back: services">
    <h2 class="back__title">services</h2>
    <div class="back__rule"></div>
    <div class="back__brand">
      <div class="brand-name"><span class="brand-dot"></span>BrightPath</div>
    </div>
    <ul class="service-list">
      <li class="service-item"><span class="service-bullet"></span>dietary &amp; fitness programs</li>
      <li class="service-item"><span class="service-bullet"></span>lymphatic &amp; therapeutic massage</li>
      <li class="service-item"><span class="service-bullet"></span>spinal exam</li>
      <li class="service-item"><span class="service-bullet"></span>health assessment</li>
      <li class="service-item"><span class="service-bullet"></span>far infrared sauna therapy</li>
      <li class="service-item"><span class="service-bullet"></span>restoration of health and vitality</li>
      <li class="service-item"><span class="service-bullet"></span>detox &amp; remineralize body wraps</li>
    </ul>
  </section>

  <section class="card card--front" aria-label="Business card front">
    <div class="front__person">
      <div class="person-name">Daniel Reyes</div>
      <div class="person-role">President</div>
    </div>
    <div class="front__brand">
      <div class="brand-name"><span class="brand-dot"></span>BrightPath</div>
      <div class="brand-sub">Chiropractic &amp; Holistic Center</div>
    </div>
    <div class="front__band">
      <ul class="contact-list">
        <li class="contact-item">
          <span class="contact-icon"><svg width="12" height="12" viewBox="0 0 24 24"><path fill="#1b9a83" d="M6.6 10.8a15 15 0 0 0 6.6 6.6l2.2-2.2c.3-.3.7-.4 1-.2 1.1.4 2.3.6 3.6.6.6 0 1 .4 1 1V20c0 .6-.4 1-1 1A17 17 0 0 1 3 4c0-.6.4-1 1-1h3.5c.6 0 1 .4 1 1 0 1.3.2 2.5.6 3.6.1.3 0 .7-.2 1z"/></svg></span>
          281-555-0193
        </li>
        <li class="contact-item">
          <span class="contact-icon"><svg width="12" height="12" viewBox="0 0 24 24"><circle cx="12" cy="12" r="9" fill="none" stroke="#1b9a83" stroke-width="2.4"/><path d="M3 12h18M12 3c3 3 3 15 0 18M12 3c-3 3-3 15 0 18" fill="none" stroke="#1b9a83" stroke-width="1.8"/></svg></span>
          www.brightpathholistic.com
        </li>
        <li class="contact-item">
          <span class="contact-icon"><svg width="12" height="12" viewBox="0 0 24 24"><rect x="2" y="5" width="20" height="14" rx="1" fill="none" stroke="#1b9a83" stroke-width="2.4"/><path d="M2 6l10 7 10-7" fill="none" stroke="#1b9a83" stroke-width="2.2"/></svg></span>
          hello@brightpathholistic.com
        </li>
        <li class="contact-item">
          <span class="contact-icon"><svg width="12" height="12" viewBox="0 0 24 24"><path fill="#1b9a83" d="M12 2a7 7 0 0 0-7 7c0 5 7 13 7 13s7-8 7-13a7 7 0 0 0-7-7zm0 9.5A2.5 2.5 0 1 1 12 6.5a2.5 2.5 0 0 1 0 5z"/></svg></span>
          Marlene Okafor LMT, 4215 Elm Ridge Rd., Suite 310, Missouri City, TX 77482
        </li>
      </ul>
    </div>
  </section>

</body>
</html>
```